Brightmill Data Works

Our company is about IT hardwares and IT solutions. IT hardware such as PC, RAMS, storage and servers. IT solutions such as project management, BA. We are also selling new technology too.

Target Market(s)

Consumer, Small to Medium Business, Corporate

Requirements
Must have
• The business card must have the following:
• Name:
• Title:
• Contact Number:
• Email address:
• Website:
• Color: Must match the logo color upgrade

```html
<!DOCTYPE html>
<html lang="en">
<head>
<meta charset="utf-8">
<title>Brightmill Data Works – Business Card</title>
<link rel="stylesheet" href="https://fonts.googleapis.com/css2?family=Lato:wght@400;700;900&display=swap">
<style>
  :root {
    --page-bg: #e8e5e2;
    --card-white: #f7f6f5;
    --band-dark: #161616;
    --accent: #c8722c;
    --accent-light: #d98a3e;
    --logo-grey: #404040;
    --text-light: #ffffff;
  }
  * { margin: 0; padding: 0; box-sizing: border-box; }
  html, body {
    width: 1200px; height: 900px; overflow: hidden;
    background: var(--page-bg);
    font-family: "Lato", Arial, sans-serif;
  }
  .business-card {
    position: absolute; left: 150px; top: 170px;
    width: 900px; height: 560px;
  }
  .card-shape { position: absolute; inset: 0; }
  .brand-mark {
    position: absolute; left: 0; top: 0; width: 536px; height: 560px;
    display: flex; flex-direction: column; align-items: center; justify-content: center;
    gap: 22px;
  }
  .brand-dot {
    width: 46px; height: 46px; border-radius: 50%; background: var(--accent);
  }
  .brand-name {
    font-weight: 900; font-size: 50px; line-height: 1.05; letter-spacing: 1px;
    text-transform: uppercase; text-align: center; color: var(--logo-grey);
  }
  .person {
    position: absolute; right: 65px; top: 70px; text-align: right;
  }
  .person-name {
    font-size: 32px; font-weight: 400; letter-spacing: 0.5px;
    color: var(--accent-light); text-transform: uppercase; line-height: 1.15;
  }
  .person-title {
    font-size: 25px; color: var(--text-light); line-height: 1.3;
  }
  .contact-list {
    position: absolute; right: 60px; top: 400px; list-style: none;
  }
  .contact-item {
    display: flex; align-items: center; justify-content: flex-end; gap: 6px;
    font-size: 25px; color: var(--text-light); height: 33px;
  }
  .contact-icon { width: 20px; height: 20px; fill: var(--accent); flex: none; }
</style>
</head>
<body>
  <div class="business-card">
    <svg class="card-shape" width="900" height="560" viewBox="0 0 900 560">
      <rect x="268" y="187" width="632" height="186" fill="var(--card-white)"/>
      <rect x="268" y="0" width="632" height="187" fill="var(--band-dark)"/>
      <rect x="268" y="373" width="632" height="187" fill="var(--band-dark)"/>
      <circle cx="268" cy="280" r="266" fill="var(--card-white)" stroke="var(--accent)" stroke-width="7"/>
    </svg>

    <div class="brand-mark">
      <span class="brand-dot"></span>
      <p class="brand-name">Brightmill<br>Data Works</p>
    </div>

    <div class="person">
      <p class="person-name">Daniel Hartley</p>
      <p class="person-title">Managing Director</p>
    </div>

    <ul class="contact-list">
      <li class="contact-item">044-555 019 277
        <svg class="contact-icon" viewBox="0 0 20 20"><path d="M2 7c0-2 2-4 8-4s8 2 8 4v2h-4V7.5c-1-.6-2.5-.8-4-.8s-3 .2-4 .8V9H2z"/><path d="M5 11l2-3h6l2 3v6H5z"/></svg>
      </li>
      <li class="contact-item">info@brightmill.com
        <svg class="contact-icon" viewBox="0 0 20 20"><path d="M2 4h16v12H2z"/><path d="M2 4l8 7 8-7" fill="none" stroke="#161616" stroke-width="1.6"/></svg>
      </li>
      <li class="contact-item">www.brightmill.com
        <svg class="contact-icon" viewBox="0 0 20 20"><circle cx="10" cy="10" r="8"/><path d="M2 10h16M10 2c3 3 3 13 0 16M10 2c-3 3-3 13 0 16" fill="none" stroke="#161616" stroke-width="1.3"/></svg>
      </li>
    </ul>
  </div>
</body>
</html>
```